Professional Website

We are looking for a new website for our Staffing Company. Attached is a document with all the details and pages needed along with some examples of others websites.

We want a professional Look and feel around the same color theme as the attached Amber Compass.

We currently host our site on PageLoom.io. If the winning designer can also add to PageLoom, that is a plus.

```html
<!DOCTYPE html>
<html lang="en">
<head>
<meta charset="utf-8">
<title>Crewline – Homepage Concepts</title>
<link href="https://fonts.googleapis.com/css2?family=Roboto:wght@400;500;700&display=swap" rel="stylesheet">
<style>
:root{
  --board:#c6c6c6;
  --blue:#2b2f9e;
  --blue-deep:#23278a;
  --ink:#1c1c1c;
  --panel-dark:#2d2d30;
  --footer:#151515;
  --heading-green:#1f4a36;
  --body-grey:#6b6b6b;
  --white:#ffffff;
  --photo-a:#5a4a3e;
  --photo-b:#2e3a55;
}
*{box-sizing:border-box;margin:0;padding:0}
html,body{width:1200px;height:1020px;overflow:hidden}
body{background:var(--board);font-family:'Roboto',sans-serif;position:relative;color:var(--ink)}

.page{position:absolute;top:95px;width:480px;background:var(--white);border-top:2px solid var(--blue);overflow:hidden}
.page--full{left:86px}
.page--short{left:634px}

/* header */
.site-header{height:34px;display:flex;align-items:center;padding:0 45px;font-size:6.6px;font-weight:500}
.brand{font-weight:700;font-size:16px;color:var(--blue);letter-spacing:-.3px;width:137px}
.nav{display:flex;align-items:center;gap:14px;flex:1}
.nav-phone{display:flex;align-items:center;gap:4px;color:var(--heading-green);font-size:7px}
.menu-icon{margin-left:auto;width:8px;height:6px;border-top:1.4px solid var(--ink);border-bottom:1.4px solid var(--ink);position:relative}
.menu-icon::after{content:"";position:absolute;left:0;right:0;top:50%;margin-top:-.7px;border-top:1.4px solid var(--ink)}

/* hero */
.hero{position:relative;height:239px;text-align:center;color:var(--white)}
.hero-photo{position:absolute;inset:0;background:linear-gradient(135deg,var(--photo-a) 0%,#7a6a5a 40%,var(--photo-b) 100%)}
.hero-shade{position:absolute;inset:0;background:rgba(20,22,40,.35)}
.hero-title{position:absolute;top:95px;left:0;right:0;font-size:23px;font-weight:500}
.hero-text{position:absolute;top:124px;left:0;right:0;font-size:7px;font-weight:500;line-height:11px}
.slide-arrow{position:absolute;top:111px;width:17px;height:17px;border-radius:50%;background:rgba(0,0,0,.55);display:flex;align-items:center;justify-content:center}
.slide-arrow--prev{left:15px}
.slide-arrow--next{right:13px}
.skew-btn{position:absolute;height:22px;display:flex;align-items:center;justify-content:center;gap:4px;color:var(--white);font-size:6.8px;font-weight:700}
.skew-btn::before{content:"";position:absolute;inset:0;background:var(--blue);transform:skewX(-14deg);z-index:0}
.skew-btn > *{position:relative;z-index:1}
.btn-start{left:198px;width:82px;top:158px}
.btn-job{left:120px;width:118px;top:158px}
.btn-hire{left:244px;width:116px;top:158px}
.btn-chip{width:17px;height:15px;background:var(--white);transform:skewX(-14deg);display:flex;align-items:center;justify-content:center;margin-right:6px}

/* choices */
.choices{position:relative;height:172px;margin-top:-12px}
.choices svg.band{position:absolute;inset:0}
.choice{position:absolute;top:0;width:240px;height:172px;text-align:center;color:var(--white)}
.choice--job{left:0}
.choice--hire{left:240px}
.choice-icon{position:absolute;left:100px;top:45px;width:40px;height:40px;border-radius:50%;background:var(--white);display:flex;align-items:center;justify-content:center}
.choice-title{position:absolute;top:96px;left:0;right:0;font-size:10.2px;font-weight:500}
.choice-rule{position:absolute;top:112px;left:102px;width:36px;border-top:1.6px solid var(--white)}
.pill{position:absolute;top:126px;left:86px;width:69px;height:17px;border-radius:9px;display:flex;align-items:center;justify-content:center;gap:3px;font-size:6px;font-weight:700;color:var(--white)}
.choice--job .pill{background:var(--ink)}
.choice--hire .pill{background:var(--blue)}

/* about */
.about{position:relative;height:245px}
.about-frame-v{position:absolute;left:38px;width:7px;background:var(--blue)}
.about-frame-h{position:absolute;left:38px;width:107px;height:7px;background:var(--blue)}
.about-photo{position:absolute;left:45px;width:188px;height:162px;background:linear-gradient(160deg,#e7eaee 0%,#9aa3ad 45%,#4a4f58 100%)}
.about-copy{position:absolute;left:264px;width:172px}
.about-copy h2{font-size:16.5px;font-weight:500;color:var(--heading-green);margin-bottom:9px}
.about-copy p{font-size:5.7px;line-height:10.6px;color:var(--body-grey);text-align:justify;margin-bottom:5px}
.btn-search{position:relative;display:inline-flex;width:66px;height:19px;margin-top:12px;align-items:center;justify-content:center;color:var(--white);font-size:6.6px;font-weight:700}
.btn-search::before{content:"";position:absolute;inset:0;background:var(--blue);transform:skewX(-14deg)}
.btn-search span{position:relative}

/* footer */
.site-footer{position:relative;height:142px;background:var(--footer);color:var(--white);font-size:5.4px}
.footer-brand{position:absolute;left:45px;top:48px;font-size:16px;font-weight:700;color:var(--blue);letter-spacing:-.3px}
.footer-badge{position:absolute;left:75px;top:71px;width:16px;height:16px;border-radius:50%;background:var(--white)}
.footer-col{position:absolute;top:25px}
.footer-col h3{font-size:6.6px;font-weight:500;margin-bottom:8px}
.col-office{left:140px}
.col-areas{left:238px}
.col-sub{left:306px;width:120px}
.contact-row{display:flex;gap:4px;margin-bottom:6px;line-height:7px}
.contact-row b{display:block;font-weight:700;font-size:4.8px}
.areas li{list-style:none;line-height:10.3px}
.sub-form{display:flex;height:18px;border-radius:9px;background:var(--white);overflow:hidden;width:119px;margin-top:-1px}
.sub-form span{flex:1;color:#8a8a8a;font-size:4.6px;display:flex;align-items:center;padding-left:9px}
.sub-form strong{width:49px;background:var(--blue);border-radius:9px;display:flex;align-items:center;justify-content:center;font-size:6.6px;font-weight:700}
.consent{display:flex;align-items:center;gap:4px;margin-top:7px;font-weight:500}
.social{display:flex;gap:5px;margin-top:8px}
.social i{width:13px;height:13px;border:.8px solid var(--white);border-radius:50%;display:block}
.footer-rule{position:absolute;left:45px;right:76px;top:112px;border-top:.6px dashed #555}
.go-up{position:absolute;left:405px;top:108px;width:31px;height:8px;border-radius:4px;background:#e9e9e9;color:var(--ink);font-size:4.4px;font-weight:700;display:flex;align-items:center;justify-content:center;gap:2px}
.footer-bottom{position:absolute;left:45px;right:45px;top:125px;display:flex;justify-content:space-between}
</style>
</head>
<body>

<!-- Homepage, full layout -->
<main class="page page--full">
  <header class="site-header">
    <div class="brand">Crewline</div>
    <nav class="nav">
      <span>Employee Login</span><span>Pay Card Login</span><span>Summit Bank Login</span>
      <span class="nav-phone"><svg width="6" height="6" viewBox="0 0 10 10"><path d="M2 1l2 2-1 1.5c.6 1.2 1.4 2 2.5 2.5L7 6l2 2-1.2 1.2C4.5 9 1 5.5.8 2.2z" fill="none" stroke="#1f4a36" stroke-width="1"/></svg>555-014-2290</span>
      <span class="menu-icon"></span>
    </nav>
  </header>

  <section class="hero">
    <div class="hero-photo" role="img" aria-label="Photo of three smiling colleagues in business attire reviewing papers at an office desk"></div>
    <div class="hero-shade"></div>
    <h1 class="hero-title">Crewline</h1>
    <p class="hero-text">We help people with our best services, Not only at work, but in life. Crewline Team<br>focuses its efforts on the Company's most valuable assets-its people.</p>
    <span class="slide-arrow slide-arrow--prev"><svg width="6" height="8" viewBox="0 0 6 8"><path d="M4.5 1 1.5 4l3 3" fill="none" stroke="#fff" stroke-width="1"/></svg></span>
    <span class="slide-arrow slide-arrow--next"><svg width="6" height="8" viewBox="0 0 6 8"><path d="M1.5 1l3 3-3 3" fill="none" stroke="#fff" stroke-width="1"/></svg></span>
    <a class="skew-btn btn-start"><span>GET STARTED</span><svg width="6" height="6" viewBox="0 0 10 10"><circle cx="5" cy="5" r="5" fill="#fff"/><path d="M4 3l2 2-2 2" fill="none" stroke="#2b2f9e" stroke-width="1.4"/></svg></a>
  </section>

  <section class="choices">
    <svg class="band" width="480" height="172" viewBox="0 0 480 172">
      <polygon points="0,0 240,37 240,172 0,172" fill="#2b2f9e"/>
      <polygon points="240,37 480,0 480,172 240,172" fill="#2d2d30"/>
    </svg>
    <div class="choice choice--job">
      <div class="choice-icon"><svg width="22" height="20" viewBox="0 0 22 20"><rect x="1" y="2" width="17" height="13" rx="1" fill="none" stroke="#2b2f9e" stroke-width="1"/><path d="M3 7h7M3 10h9M3 12h6" stroke="#2b2f9e" stroke-width=".8"/><circle cx="16" cy="13" r="3.2" fill="#fff" stroke="#2b2f9e" stroke-width="1"/><path d="M18.3 15.3 21 18" stroke="#2b2f9e" stroke-width="1.2"/></svg></div>
      <div class="choice-title">I'M LOOKING FOR A JOB</div>
      <div class="choice-rule"></div>
      <a class="pill">LEARN MORE <svg width="5" height="5" viewBox="0 0 10 10"><circle cx="5" cy="5" r="5" fill="#fff"/><path d="M4 3l2 2-2 2" fill="none" stroke="#1c1c1c" stroke-width="1.4"/></svg></a>
    </div>
    <div class="choice choice--hire">
      <div class="choice-icon"><svg width="22" height="20" viewBox="0 0 22 20"><circle cx="11" cy="5" r="2.5" fill="none" stroke="#1c1c1c" stroke-width=".9"/><circle cx="5" cy="8" r="2.2" fill="none" stroke="#1c1c1c" stroke-width=".9"/><circle cx="17" cy="8" r="2.2" fill="none" stroke="#1c1c1c" stroke-width=".9"/><path d="M7 18v-6c0-2 8-2 8 0v6M1.5 18v-5c0-1.6 4-2 5-1M20.5 18v-5c0-1.6-4-2-5-1" fill="none" stroke="#1c1c1c" stroke-width=".9"/></svg></div>
      <div class="choice-title">I NEED EMPLOYEES</div>
      <div class="choice-rule"></div>
      <a class="pill">LEARN MORE <svg width="5" height="5" viewBox="0 0 10 10"><circle cx="5" cy="5" r="5" fill="#fff"/><path d="M4 3l2 2-2 2" fill="none" stroke="#2b2f9e" stroke-width="1.4"/></svg></a>
    </div>
  </section>

  <section class="about">
    <div class="about-frame-v" style="top:106px;height:103px"></div>
    <div class="about-frame-h" style="top:202px"></div>
    <div class="about-photo" style="top:40px" role="img" aria-label="Photo of three business colleagues discussing a tablet in a bright office"></div>
    <div class="about-copy" style="top:44px">
      <h2>About Us</h2>
      <p>Greatest part of our daily job is that we are constantly bringing people together. Our Clients come to us in search of the perfect candidate and the job hunters approach us when they are in need of a job or looking for their next exciting role. Being able to work with and connect the two is incredibly satisfying.</p>
      <p>Not to mention that in today's current job market, employers are fighting for the top talent. This makes our employees and partners grateful for the help in finding it!</p>
      <a class="btn-search"><span>SEARCH JOBS</span></a>
    </div>
  </section>

  <footer class="site-footer">
    <div class="footer-brand">Crewline</div>
    <div class="footer-badge"></div>
    <div class="footer-col col-office">
      <h3>Our Office Address</h3>
      <div class="contact-row"><svg width="5" height="5" viewBox="0 0 10 10"><path d="M2 1l2 2-1 1.5c.6 1.2 1.4 2 2.5 2.5L7 6l2 2-1.2 1.2C4.5 9 1 5.5.8 2.2z" fill="#3a46c8"/></svg><div><b>Phone</b>(555) 014-2290</div></div>
      <div class="contact-row"><svg width="5" height="5" viewBox="0 0 10 8"><rect width="10" height="8" fill="#3a46c8"/><path d="M0 0l5 4 5-4" fill="none" stroke="#151515" stroke-width="1"/></svg><div><b>Email</b>hello@crewlinestaff.com</div></div>
      <div class="contact-row"><svg width="5" height="6" viewBox="0 0 8 10"><path d="M4 10S0 5.5 0 3.8a4 4 0 0 1 8 0C8 5.5 4 10 4 10z" fill="#3a46c8"/></svg><div><b>Location</b>P.O.BOX 418 OAKRIDGE IL 60000</div></div>
    </div>
    <div class="footer-col col-areas">
      <h3>Areas we service</h3>
      <ul class="areas"><li>Maple Ridge</li><li>Eastbrook</li><li>Cedarville</li><li>North Haven IL</li><li>Willow Park IL</li><li>Stonefield IN</li></ul>
    </div>
    <div class="footer-col col-sub">
      <h3>Subscribe for Updates</h3>
      <div class="sub-form"><span>Email Address</span><strong>SUBMIT</strong></div>
      <div class="consent"><svg width="5" height="5" viewBox="0 0 10 10"><rect x=".5" y=".5" width="9" height="9" fill="none" stroke="#fff"/><path d="M2 5l2 2 4-4" fill="none" stroke="#fff" stroke-width="1.3"/></svg>Yes, Please Contact me.</div>
      <div class="social"><i></i><i></i><i></i></div>
    </div>
    <div class="footer-rule"></div>
    <div class="go-up">&#8593; Go Up</div>
    <div class="footer-bottom"><span>© 2022 crewlinestaff | All Rights Reserved</span><span>Privacy Policy &nbsp;| &nbsp;Cookie Policy &nbsp;| &nbsp;Terms Of Services</span></div>
  </footer>
</main>

<!-- Homepage, short layout -->
<main class="page page--short">
  <header class="site-header">
    <div class="brand">Crewline</div>
    <nav class="nav">
      <span>Employee Login</span><span>Pay Card Login</span><span>Summit Bank Login</span>
      <span class="nav-phone"><svg width="6" height="6" viewBox="0 0 10 10"><path d="M2 1l2 2-1 1.5c.6 1.2 1.4 2 2.5 2.5L7 6l2 2-1.2 1.2C4.5 9 1 5.5.8 2.2z" fill="none" stroke="#1f4a36" stroke-width="1"/></svg>555-014-2290</span>
      <span class="menu-icon"></span>
    </nav>
  </header>

  <section class="hero">
    <div class="hero-photo" role="img" aria-label="Photo of three smiling colleagues in business attire reviewing papers at an office desk"></div>
    <div class="hero-shade"></div>
    <h1 class="hero-title">Crewline</h1>
    <p class="hero-text">We help people with our best services, Not only at work, but in life. Crewline Team<br>focuses its efforts on the Company's most valuable assets-its people.</p>
    <span class="slide-arrow slide-arrow--prev"><svg width="6" height="8" viewBox="0 0 6 8"><path d="M4.5 1 1.5 4l3 3" fill="none" stroke="#fff" stroke-width="1"/></svg></span>
    <span class="slide-arrow slide-arrow--next"><svg width="6" height="8" viewBox="0 0 6 8"><path d="M1.5 1l3 3-3 3" fill="none" stroke="#fff" stroke-width="1"/></svg></span>
    <a class="skew-btn btn-job"><span class="btn-chip"><svg width="9" height="9" viewBox="0 0 10 10"><circle cx="5" cy="3" r="2" fill="none" stroke="#2b2f9e" stroke-width=".9"/><rect x="1.5" y="6" width="7" height="3.5" fill="none" stroke="#2b2f9e" stroke-width=".9"/></svg></span><span>I'M LOOKING FOR A JOB</span></a>
    <a class="skew-btn btn-hire"><span class="btn-chip"><svg width="10" height="9" viewBox="0 0 12 10"><circle cx="6" cy="3" r="1.6" fill="none" stroke="#2b2f9e" stroke-width=".8"/><circle cx="2.5" cy="4" r="1.3" fill="none" stroke="#2b2f9e" stroke-width=".8"/><circle cx="9.5" cy="4" r="1.3" fill="none" stroke="#2b2f9e" stroke-width=".8"/><path d="M3.5 9.5V7c0-1.2 5-1.2 5 0v2.5" fill="none" stroke="#2b2f9e" stroke-width=".8"/></svg></span><span>I NEED EMPLOYEES</span></a>
  </section>

  <section class="about" style="height:243px">
    <div class="about-frame-v" style="top:102px;height:103px"></div>
    <div class="about-frame-h" style="top:198px"></div>
    <div class="about-photo" style="top:35px" role="img" aria-label="Photo of three business colleagues discussing a tablet in a bright office"></div>
    <div class="about-copy" style="top:39px">
      <h2>About Us</h2>
      <p>Greatest part of our daily job is that we are constantly bringing people together. Our Clients come to us in search of the perfect candidate and the job hunters approach us when they are in need of a job or looking for their next exciting role. Being able to work with and connect the two is incredibly satisfying.</p>
      <p>Not to mention that in today's current job market, employers are fighting for the top talent. This makes our employees and partners grateful for the help in finding it!</p>
      <a class="btn-search"><span>SEARCH JOBS</span></a>
    </div>
  </section>

  <footer class="site-footer">
    <div class="footer-brand">Crewline</div>
    <div class="footer-badge"></div>
    <div class="footer-col col-office">
      <h3>Our Office Address</h3>
      <div class="contact-row"><svg width="5" height="5" viewBox="0 0 10 10"><path d="M2 1l2 2-1 1.5c.6 1.2 1.4 2 2.5 2.5L7 6l2 2-1.2 1.2C4.5 9 1 5.5.8 2.2z" fill="#3a46c8"/></svg><div><b>Phone</b>(555) 014-2290</div></div>
      <div class="contact-row"><svg width="5" height="5" viewBox="0 0 10 8"><rect width="10" height="8" fill="#3a46c8"/><path d="M0 0l5 4 5-4" fill="none" stroke="#151515" stroke-width="1"/></svg><div><b>Email</b>hello@crewlinestaff.com</div></div>
      <div class="contact-row"><svg width="5" height="6" viewBox="0 0 8 10"><path d="M4 10S0 5.5 0 3.8a4 4 0 0 1 8 0C8 5.5 4 10 4 10z" fill="#3a46c8"/></svg><div><b>Location</b>P.O.BOX 418 OAKRIDGE IL 60000</div></div>
    </div>
    <div class="footer-col col-areas">
      <h3>Areas we service</h3>
      <ul class="areas"><li>Maple Ridge</li><li>Eastbrook</li><li>Cedarville</li><li>North Haven IL</li><li>Willow Park IL</li><li>Stonefield IN</li></ul>
    </div>
    <div class="footer-col col-sub">
      <h3>Subscribe for Updates</h3>
      <div class="sub-form"><span>Email Address</span><strong>SUBMIT</strong></div>
      <div class="consent"><svg width="5" height="5" viewBox="0 0 10 10"><rect x=".5" y=".5" width="9" height="9" fill="none" stroke="#fff"/><path d="M2 5l2 2 4-4" fill="none" stroke="#fff" stroke-width="1.3"/></svg>Yes, Please Contact me.</div>
      <div class="social"><i></i><i></i><i></i></div>
    </div>
    <div class="footer-rule"></div>
    <div class="go-up">&#8593; Go Up</div>
    <div class="footer-bottom"><span>© 2022 crewlinestaff | All Rights Reserved</span><span>Privacy Policy &nbsp;| &nbsp;Cookie Policy &nbsp;| &nbsp;Terms Of Services</span></div>
  </footer>
</main>

</body>
</html>
```